Heritage Hollow Business Cards

Require a business card design. <br/><br/>Needs to include logo (either round or long version) plus these details:<br/>Maya Torvell<br/>Heritage Hollow<br/>maya@kelvadtrading.com.au<br/>02 6481 7395<br/>PO Box Glenwarra NSW 2791<br/>www.heritagehollow.com.au<br/><br/>I need in an editable format so that I can create for multiple staff members. <br/><br/>

Target Market(s)

We are an online store selling renovation products to home owners are builders. Looking for a classic classy design.

Industry/Entity Type

Home And Garden

Contact Information for Business Card

Maya Torvell
Heritage Hollow
maya@kelvadtrading.com.au
02 6481 7395
PO Box Glenwarra NSW 2791
www.heritagehollow.com.au

Colors

Designer to choose colors to be used in the design.

Requirements
Must have
• Must include Logo.

```html
<!DOCTYPE html>
<html lang="en">
<head>
<meta charset="utf-8">
<title>Heritage Hollow Business Cards</title>
<link rel="stylesheet" href="https://fonts.googleapis.com/css2?family=Arimo:wght@400;700&display=swap">
<style>
  :root {
    --backdrop: #d9d9d9;
    --card-black: #1f1c1d;
    --card-white: #ffffff;
    --ink: #1a1a1a;
    --ink-soft: #2b2b2b;
    --silver: #d8d8d8;
    --rule: #cfcfcf;
  }
  * { box-sizing: border-box; margin: 0; padding: 0; }
  html, body {
    width: 1200px; height: 1015px; overflow: hidden;
    background: var(--backdrop);
    font-family: "Arimo", Arial, sans-serif;
  }
  .sheet {
    width: 1200px; height: 1015px;
    display: flex; flex-direction: column; align-items: center; justify-content: center;
    gap: 56px;
  }
  .card {
    width: 760px; height: 434px; position: relative; overflow: hidden;
    box-shadow: 0 6px 18px rgba(0,0,0,0.25);
  }
  /* Front */
  .card--front { background: var(--card-black); display: flex; align-items: center; justify-content: center; }
  .brand { display: flex; align-items: center; gap: 18px; }
  .brand__circle { width: 74px; height: 74px; border-radius: 50%; border: 2px solid currentColor; }
  .brand__name { font-weight: 400; letter-spacing: 0.5px; }
  .card--front .brand { color: var(--silver); }
  .card--front .brand__name { font-size: 50px; }
  /* Back */
  .card--back { background: var(--card-white); }
  .back__body { position: absolute; inset: 0 0 124px 0; display: flex; }
  .back__logo { width: 48%; display: flex; align-items: center; justify-content: center; padding-top: 40px; }
  .card--back .brand { color: var(--ink-soft); gap: 12px; }
  .card--back .brand__circle { width: 44px; height: 44px; border-width: 1.5px; }
  .card--back .brand__name { font-size: 28px; }
  .back__divider { width: 1px; background: var(--rule); margin: 0; }
  .back__details { flex: 1; padding: 44px 0 0 40px; color: var(--ink); }
  .person { font-size: 23px; font-weight: 700; letter-spacing: 0.6px; text-transform: uppercase; margin-bottom: 12px; }
  .contact { list-style: none; font-size: 19px; line-height: 1.3; }
  .contact li { display: flex; align-items: center; gap: 6px; }
  .contact svg { width: 18px; height: 18px; flex: none; }
  .address { margin-top: 14px; font-size: 19px; line-height: 1.25; }
  .back__band {
    position: absolute; left: 0; right: 0; bottom: 0; height: 124px;
    background: var(--card-black); color: #f2f2f2;
    display: flex; align-items: center; justify-content: center;
    font-size: 24px; letter-spacing: 0.8px;
  }
</style>
</head>
<body>
<main class="sheet">
  <section class="card card--front" aria-label="Card front">
    <div class="brand">
      <span class="brand__circle"></span>
      <span class="brand__name">Heritage Hollow</span>
    </div>
  </section>

  <section class="card card--back" aria-label="Card back">
    <div class="back__body">
      <div class="back__logo">
        <div class="brand">
          <span class="brand__circle"></span>
          <span class="brand__name">Heritage Hollow</span>
        </div>
      </div>
      <div class="back__divider"></div>
      <div class="back__details">
        <p class="person">Maya Torvell</p>
        <ul class="contact">
          <li>
            <svg viewBox="0 0 18 18" aria-hidden="true"><rect x="1" y="1" width="16" height="16" rx="3" fill="none" stroke="currentColor" stroke-width="1.6"/><path d="M6 4.5c-1 .6-1.3 1.8-.6 3.4.9 2 2.6 3.7 4.6 4.6 1.6.7 2.8.4 3.4-.6l-1.7-1.6-1.3.8c-1.3-.6-2.4-1.7-3-3l.8-1.3z" fill="currentColor"/></svg>
            02 6481 7395
          </li>
          <li>
            <svg viewBox="0 0 18 18" aria-hidden="true"><rect x="1" y="4" width="16" height="11" fill="currentColor"/><path d="M1 4l8 6 8-6" fill="none" stroke="#fff" stroke-width="1.3"/></svg>
            maya@kelvadtrading.com.au
          </li>
        </ul>
        <p class="address">PO Box Glenwarra<br>NSW 2791</p>
      </div>
    </div>
    <div class="back__band">www.heritagehollow.com.au</div>
  </section>
</main>
</body>
</html>
```